Bring me business with this creative business card

Design my new business card. I am looking for something different with an impact. People will take a look at this card & they will 1- see how different & creative I am, 2-understand what I do 3- Call me to meet me!

I make videos with a message, testimonials. I am dynamic, fun, creative & human. My new website is in construction but in the meantime you can check this old one: brightpath.ca & another one Tidebloom.com & tidebloom facebook page.
I make videos. sometimes with a cameraman, sometimes with my phone. As an ex Public Relations agent, the message is the most important thing for me. I want to make my clients shine! When they start with me they often remind me of a lamb, when I finish coaching them they are powerful like LIONS! That's why I need a powerful business card!

Target Market(s)

Entrepreneurs, solo entrepreneurs, small & medium companies & start ups. People i will meet while networking. People that need videos on their website & social Networks to get attention, to be visible. men & women. From 35 to 49 years old.
I am an ex Public relations agent. I used to send clients in traditional medias, now with videos they have more chances to be seen on google the new media. I do videos of the president, his team, his loyal clients saying how great the company is & expert videos like series so people can be seen for example every 1 st of every month with a short 2 minute video. Also with my 20 years in marketing & communications I can coach & give tips to anybody who needs it.
Target: anybody who would like my old website brightpath.ca & I also have another website but it will be off line soon: tidebloom.com could give you ideas.

Industry/Entity Type

Communications

Contact Information for Business Card

I am in Montreal,So the business cards have to be the usual size like we have in Montreal: 9 cm x 5 cm
Details:My text: Mathilde Tessier Communication coach/Chief Bloom. "Shaping stories as vivid as you" off: 514-555-0147 cell: 514-555-0183. tidebloom.com
mathilde@tidebloom.com logo facebook, youtube, instagram

Colors
f37122

Requirements
Must have
• Dynamic, happy. Orange. Be creative in the look but NOT the shape of the card. Easy to read. Big enough to read.
Should not have
• No funny shapes: no round, no square, just the usual. I love creative but NOT on shape.

```html
<!DOCTYPE html>
<html lang="en">
<head>
<meta charset="utf-8">
<title>Tidebloom – Business Card</title>
<link href="https://fonts.googleapis.com/css2?family=Cinzel:wght@600&family=Lato:wght@400&family=Tinos:wght@400;700&display=swap" rel="stylesheet">
<style>
  :root {
    --stage: #2e2e2e;
    --paper: #ffffff;
    --orange: #f37122;
    --orange-deep: #ef5f22;
    --orange-light: #f5951f;
    --ink: #1c1c1c;
    --white: #ffffff;
  }
  * { margin: 0; padding: 0; box-sizing: border-box; }
  html, body { width: 1200px; height: 900px; overflow: hidden; }
  body { background: var(--stage); position: relative; }

  .card {
    position: absolute;
    top: 170px;
    width: 347px;
    height: 561px;
  }

  /* Front */
  .card-front { left: 259px; background: var(--paper); text-align: center; }
  .brand-mark {
    position: absolute; left: 123px; top: 72px;
    width: 100px; height: 100px; border-radius: 50%;
    background: var(--orange);
  }
  .brand-name {
    position: absolute; left: 0; right: 0; top: 206px;
    font-family: "Cinzel", serif; font-weight: 600;
    font-size: 32px; letter-spacing: 1px; color: var(--orange);
  }
  .holder-name {
    position: absolute; left: 0; right: 0; top: 340px;
    font-family: "Tinos", serif; font-weight: 700;
    font-size: 23px; letter-spacing: 0.5px; color: var(--orange);
  }
  .holder-title {
    position: absolute; left: 0; right: 0; top: 366px;
    font-family: "Lato", sans-serif; font-size: 15.5px; color: var(--ink);
  }
  .divider {
    position: absolute; left: 88px; top: 403px;
    width: 172px; height: 1.5px; background: var(--orange);
  }
  .contact-icons {
    position: absolute; left: 0; right: 0; top: 426px;
    display: flex; justify-content: center; gap: 4px;
  }
  .contact-icons svg { width: 17px; height: 17px; }
  .contact-list {
    position: absolute; left: 0; right: 0; top: 445px;
    list-style: none;
    font-family: "Lato", sans-serif; font-size: 15px;
    line-height: 20px; color: var(--ink);
  }

  /* Back */
  .card-back {
    left: 631px;
    background: radial-gradient(ellipse at 50% 45%, var(--orange-deep) 0%, var(--orange) 45%, var(--orange-light) 100%);
    color: var(--white);
    font-family: "Tinos", serif;
  }
  .slogan {
    position: absolute; left: 46px; top: 130px; width: 258px;
  }
  .slogan-line {
    display: block; font-size: 47px; line-height: 63px;
    letter-spacing: 1px; white-space: nowrap;
  }
  .slogan-you {
    display: block; font-size: 92px; line-height: 100px;
    letter-spacing: 26px; margin-top: 14px; white-space: nowrap;
  }
</style>
</head>
<body>

<section class="card card-front" aria-label="Business card front">
  <div class="brand-mark"></div>
  <div class="brand-name">TIDEBLOOM</div>

  <div class="holder-name">MATHILDE T</div>
  <div class="holder-title">Communication Coach/Chief Bloom</div>
  <div class="divider"></div>

  <div class="contact-icons">
    <svg viewBox="0 0 20 20" aria-label="Office phone"><circle cx="10" cy="10" r="10" fill="#f37122"/><path d="M5 8.5c0-2 10-2 10 0v1.5h-3V8.5h-4V10H5z M6.5 11h7v3.5h-7z" fill="#fff"/></svg>
    <svg viewBox="0 0 20 20" aria-label="Mobile phone"><circle cx="10" cy="10" r="10" fill="#f37122"/><rect x="6.5" y="4.5" width="7" height="11" rx="1" fill="#fff"/><rect x="7.7" y="6" width="4.6" height="7" fill="#f37122"/></svg>
    <svg viewBox="0 0 20 20" aria-label="Email"><circle cx="10" cy="10" r="10" fill="#f37122"/><rect x="5" y="6.5" width="10" height="7" fill="#fff"/><path d="M5 6.5l5 4 5-4" fill="none" stroke="#f37122" stroke-width="1"/></svg>
    <svg viewBox="0 0 20 20" aria-label="Website"><circle cx="10" cy="10" r="10" fill="#f37122"/><circle cx="10" cy="10" r="5" fill="none" stroke="#fff" stroke-width="1.4"/><path d="M5 10h10M10 5c-2.5 3-2.5 7 0 10M10 5c2.5 3 2.5 7 0 10" fill="none" stroke="#fff" stroke-width="1"/></svg>
  </div>

  <ul class="contact-list">
    <li>514-555-0147</li>
    <li>514-555-0183</li>
    <li>mathilde@tidebloom.com</li>
    <li>www.tidebloom.com</li>
  </ul>
</section>

<section class="card card-back" aria-label="Business card back">
  <p class="slogan">
    <span class="slogan-line">SHAPING</span>
    <span class="slogan-line">STORIES AS</span>
    <span class="slogan-line">VIVID AS</span>
    <span class="slogan-you">YOU</span>
  </p>
</section>

</body>
</html>
```